KPV Datacore Solutions

We need a Logo and Website for our company based in London. We are a IT recruitment company . We provide quality resources to top IT company across UK.

Industry/Entity Type

It Company

Number of Pages Required

4 page

```html
<!DOCTYPE html>
<html lang="en">
<head>
<meta charset="utf-8">
<title>KPV Datacore Solutions</title>
<link href="https://fonts.googleapis.com/css2?family=Old+Standard+TT:wght@700&family=Open+Sans:wght@400;600;700&display=swap" rel="stylesheet">
<style>
:root{
  --orange:#f7821b;
  --blue:#0c6fc0;
  --dark:#1c1c1c;
  --nav:#111111;
  --text:#222;
  --muted:#777;
  --line:#4a4a4a;
  --white:#fff;
}
*{margin:0;padding:0;box-sizing:border-box}
html,body{width:684px;height:1200px;overflow:hidden;background:var(--white)}
body{position:relative;font-family:"Open Sans",Arial,sans-serif;color:var(--text)}
.abs{position:absolute}
.serif{font-family:"Old Standard TT",Georgia,serif;font-weight:700}
.orange{color:var(--orange)}
.blue{color:var(--blue)}

/* header */
.header{left:0;top:0;width:684px;height:58px;background:var(--white)}
.call{left:26px;top:19px;display:flex;align-items:center;gap:6px}
.call-icon{width:22px;height:22px;border:1.5px solid var(--blue);border-radius:50%;display:flex;align-items:center;justify-content:center}
.call-label{font-size:6px;color:var(--blue);line-height:1}
.call-number{font-size:10px;color:#111;line-height:1.3}
.brand{left:300px;top:18px;display:flex;align-items:center;gap:6px}
.brand-mark{width:20px;height:20px;background:var(--orange)}
.brand-name{font-size:10.5px;line-height:12px;font-weight:700;color:var(--orange);letter-spacing:1.5px;text-transform:uppercase}
.social{left:589px;top:21px;display:flex;gap:8px}
.social span{width:16px;height:16px;border-radius:50%;border:1px solid var(--blue)}
.social span.filled{background:var(--blue)}

/* nav */
.nav{left:0;top:58px;width:684px;height:39px;background:var(--nav)}
.nav a{position:absolute;top:17px;font-size:7.5px;color:var(--blue);text-decoration:none;text-transform:uppercase}
.nav a.active{color:var(--orange)}

/* hero */
.hero{left:0;top:97px;width:684px;height:292px;background:linear-gradient(100deg,#2e2e2e 0%,#3a3a3c 45%,#55585c 75%,#3d3e40 100%)}
.hero-title{left:30px;top:86px;font-size:24.5px;line-height:26px;color:var(--white);white-space:nowrap}
.hero-text{left:30px;top:143px;width:415px;font-size:8.4px;line-height:13px;color:#e6e6e6}
.btn{background:var(--orange);color:var(--white);font-size:6.5px;text-transform:uppercase;display:flex;align-items:center;justify-content:center}
.hero-btn{left:30px;top:195px;width:78px;height:24px}
.dots{left:427px;top:265px;display:flex;gap:4px}
.dots span{width:7px;height:7px;border-radius:50%;background:var(--white)}
.dots span.on{background:var(--orange)}

/* welcome */
.welcome-title{left:0;width:684px;top:414px;text-align:center;font-size:22px;color:#111;white-space:nowrap}
.welcome-text{left:58px;width:568px;top:453px;text-align:center;font-size:6.3px;line-height:12px;color:var(--muted)}
.welcome-btn{left:305px;top:501px;width:69px;height:21px}

/* services */
.services{left:0;top:557px;width:684px;height:447px;background:var(--dark)}
.services-title{left:0;width:684px;top:22px;text-align:center;font-size:21px;color:var(--white)}
.timeline{left:339px;top:63px;width:1px;height:346px;background:var(--line)}
.branch{height:1px;background:var(--line)}
.badge{width:66px;height:66px;border-radius:50%;border:2px solid var(--orange);background:var(--blue);display:flex;align-items:center;justify-content:center}
.badge.alt{background:var(--orange);border-color:var(--blue)}
.svc h3{font-size:11px;font-weight:600;color:var(--blue);margin-bottom:6px}
.svc p{font-size:6.6px;line-height:11px;color:#e8e8e8}
.svc .more{font-size:6.5px;font-weight:700;color:var(--blue);margin-top:4px;text-transform:uppercase}
.svc .more.o{color:var(--orange)}
.svc.left{text-align:right}

/* profile */
.profile-title{left:0;width:684px;top:1021px;text-align:center;font-size:21px;color:#111}
.client{top:1082px;width:105px;height:40px;border:1px solid #e3e3e3;display:flex;align-items:center;justify-content:center;gap:5px;font-size:12px;font-weight:600;color:#444}
.client i{width:8px;height:8px;background:var(--blue);display:block}
.arrow{top:1092px;width:15px;height:18px;background:#eee;border:1px solid #ddd;display:flex;align-items:center;justify-content:center}

/* footer */
.footer{left:0;top:1156px;width:684px;height:44px;background:var(--blue);border-top:2px solid var(--orange)}
.footer-text{left:0;width:684px;top:18px;text-align:center;font-size:5.2px;color:var(--white)}
.footer-social{right:22px;top:17px;display:flex;gap:13px}
.footer-social span{width:7px;height:7px;border-radius:50%;background:var(--white)}
.footer-social span.rss{background:var(--orange)}
</style>
</head>
<body>

<header class="abs header">
  <div class="abs call">
    <div class="call-icon">
      <svg width="11" height="11" viewBox="0 0 24 24"><path d="M6.6 10.8c1.4 2.8 3.8 5.1 6.6 6.6l2.2-2.2c.3-.3.7-.4 1-.2 1.1.4 2.3.6 3.6.6.6 0 1 .4 1 1V20c0 .6-.4 1-1 1C10.6 21 3 13.4 3 4c0-.6.4-1 1-1h3.5c.6 0 1 .4 1 1 0 1.3.2 2.5.6 3.6.1.3 0 .7-.2 1z" fill="var(--blue)"/></svg>
    </div>
    <div>
      <div class="call-label">Call Us</div>
      <div class="call-number">1234-567-890</div>
    </div>
  </div>
  <div class="abs brand">
    <span class="brand-mark"></span>
    <span class="brand-name">KPV Datacore<br>Solutions</span>
  </div>
  <div class="abs social">
    <span class="filled"></span><span></span><span></span>
  </div>
</header>

<nav class="abs nav">
  <a class="active" style="left:114px">Home</a>
  <a style="left:172px">About Us</a>
  <a style="left:250px">How We Can Help</a>
  <a style="left:347px">Our Serivers</a>
  <a style="left:428px">Our Portfolio</a>
  <a style="left:525px">Contact Us</a>
</nav>

<section class="abs hero" role="img" aria-label="Dimmed photo of hands typing on a laptop keyboard">
  <h1 class="abs hero-title serif"><span class="orange">Lorem Lpsum</span> Dolor Sit Amet<br><span class="orange">Consectetur Adipiscing</span> Elit Eiusmod</h1>
  <p class="abs hero-text">Lorem ipsum dolor sit amet, consectetur adipiscing elit, sed do eiusmod tempor incididunt ut labore et dolore magna aliqua. Ut enim ad minim veniam, quis nostrud exercitation ullamco laboris nisi ut aliquip ex ea commodo consequat. Duis aute irure dolor in reprehenderit in voluptate</p>
  <div class="abs btn hero-btn">Read More</div>
  <div class="abs dots"><span></span><span class="on"></span><span></span></div>
</section>

<h2 class="abs welcome-title serif">Welcome to <span class="orange">KPV</span> <span class="blue">Datacore Solutions</span></h2>
<p class="abs welcome-text">Lorem ipsum dolor sit amet, consectetur adipiscing elit, sed do eiusmod tempor incididunt ut labore et dolore magna aliqua. Ut enim ad minim veniam, quis nostrud exercitation ullamco laboris nisi ut aliquip ex ea commodo consequat. Duis aute irure dolor in reprehenderit in voluptate velit esse cillum dolore eu fugiat nulla pariatur. Excepteur sint occaecat cupidatat non proident, sunt in culpa qui officia deserunt mollit anim id est laborum.</p>
<div class="abs btn welcome-btn">Read More</div>

<section class="abs services">
  <h2 class="abs services-title serif">Our <span class="blue">Service</span></h2>
  <div class="abs timeline"></div>
  <svg class="abs" style="left:335px;top:60px" width="9" height="6"><path d="M0.5 5.5 4.5 1 8.5 5.5" fill="none" stroke="#4a4a4a"/></svg>

  <div class="abs branch" style="left:339px;top:108px;width:26px"></div>
  <div class="abs branch" style="left:311px;top:152px;width:28px"></div>
  <div class="abs branch" style="left:339px;top:210px;width:26px"></div>
  <div class="abs branch" style="left:311px;top:270px;width:28px"></div>
  <div class="abs branch" style="left:339px;top:343px;width:26px"></div>

  <div class="abs badge alt" style="left:365px;top:75px">
    <svg width="30" height="28" viewBox="0 0 30 28" fill="none" stroke="#fff" stroke-width="2" stroke-linejoin="round"><path d="M9 3h9v8H9z M3 13h9v8H3z M15 13h9v8h-9z"/><circle cx="25" cy="23" r="2.5"/></svg>
  </div>
  <div class="abs svc" style="left:443px;top:77px;width:205px">
    <h3>Lorem ipsum dolor</h3>
    <p>Early stage companies have great ideas but often times cannot bootstrap themselves to profitability. Other companies have customers and revenue, but want to invest</p>
    <div class="more o">Read More ▸</div>
  </div>

  <div class="abs badge" style="left:245px;top:119px">
    <svg width="28" height="28" viewBox="0 0 28 28"><circle cx="14" cy="14" r="12" fill="#fff"/><path d="M14 9l4 3-1.5 5h-5L10 12z" fill="var(--blue)"/></svg>
  </div>
  <div class="abs svc left" style="left:40px;top:121px;width:198px">
    <h3>Lorem ipsum dolor</h3>
    <p>We have worked with both large and small internet companies, and have grown companies to become market leaders in their sectors. We understand the inner workings</p>
    <div class="more">Read More ▸</div>
  </div>

  <div class="abs badge" style="left:365px;top:177px">
    <svg width="24" height="28" viewBox="0 0 24 28" fill="none" stroke="#fff" stroke-width="2"><path d="M3 2h12l6 6v18H3z M15 2v6h6 M7 14h10 M7 18h10 M7 22h10"/></svg>
  </div>
  <div class="abs svc" style="left:443px;top:179px;width:200px">
    <h3>Lorem ipsum dolor</h3>
    <p>We dedicate time on-site to our portfolio companies, and will arrange and attend key meetings with strategic partners or clients. Informal mentorship and advice through</p>
    <div class="more">Read More ▸</div>
  </div>

  <div class="abs badge" style="left:245px;top:237px">
    <svg width="30" height="28" viewBox="0 0 30 28" fill="#fff"><circle cx="11" cy="16" r="7"/><circle cx="11" cy="16" r="3" fill="var(--blue)"/><circle cx="22" cy="8" r="5"/><circle cx="22" cy="8" r="2" fill="var(--blue)"/><circle cx="23" cy="21" r="4"/><circle cx="23" cy="21" r="1.5" fill="var(--blue)"/></svg>
  </div>
  <div class="abs svc left" style="left:34px;top:238px;width:204px">
    <h3>Lorem ipsum dolor</h3>
    <p>Calderwyn Ventures has key relationships in large web companies in Australia, the US, and the UK. These connections are critical to helping start the dialogue to create key</p>
    <div class="more">Read More ▸</div>
  </div>

  <div class="abs badge" style="left:365px;top:310px">
    <svg width="28" height="24" viewBox="0 0 28 24"><path d="M11 2 2 10l9 8v-5c7 0 11 2 14 8 0-8-4-14-14-15z" fill="#fff"/></svg>
  </div>
  <div class="abs svc" style="left:443px;top:312px;width:205px">
    <h3>Lorem ipsum dolor</h3>
    <p>We have been on the buying side from big media companies and know how they evaluate and process acquisitions. We can help ensure that you build it the right way</p>
    <div class="more">Read More ▸</div>
  </div>
</section>

<h2 class="abs profile-title serif">Our <span class="blue">Profile</span></h2>
<div class="abs arrow" style="left:27px"><svg width="5" height="8"><path d="M4 1 1 4l3 3" fill="none" stroke="#999"/></svg></div>
<div class="abs client" style="left:61px"><i></i>Quillmere</div>
<div class="abs client" style="left:174px">Vantrosk</div>
<div class="abs client" style="left:289px">Orbelline</div>
<div class="abs client" style="left:404px">Hirozent</div>
<div class="abs client" style="left:519px"><i></i>Plemwick</div>
<div class="abs arrow" style="left:642px"><svg width="5" height="8"><path d="M1 1l3 3-3 3" fill="none" stroke="#999"/></svg></div>

<footer class="abs footer">
  <p class="abs footer-text">© All Rights Reserved. Copyrights @KPV Datacore Solutions . 2016</p>
  <div class="abs footer-social"><span class="rss"></span><span></span><span></span><span></span><span></span></div>
</footer>

</body>
</html>
```